Construction business card

I need a new business card, they can connect with my logo, brand.
What we do is residential house , design and build
I like: Navy blue / black
I attached our logo, brand,
and, some idea for business card.

```html
<!DOCTYPE html>
<html lang="en">
<head>
<meta charset="utf-8">
<title>Harwell Building Group – Business Card</title>
<link href="https://fonts.googleapis.com/css2?family=Arimo:wght@400;700&display=swap" rel="stylesheet">
<style>
  :root {
    --stage: #1f1f20;
    --card-blue: #3b88c9;
    --ink: #ffffff;
    --rule: rgba(255,255,255,0.85);
  }
  * { margin: 0; padding: 0; box-sizing: border-box; }
  html, body { width: 1200px; height: 801px; overflow: hidden; background: var(--stage); }
  body {
    font-family: "Arimo", Arial, sans-serif;
    color: var(--ink);
    display: flex;
    align-items: center;
    justify-content: center;
    gap: 40px;
  }
  .card {
    position: relative;
    width: 540px;
    height: 310px;
    background: var(--card-blue);
    border-radius: 22px;
    overflow: hidden;
  }

  /* Front: details side */
  .brand-mark {
    position: absolute;
    left: 150px;
    top: 62px;
    display: flex;
    align-items: center;
    gap: 8px;
    font-weight: 700;
    font-size: 22px;
    letter-spacing: 0.5px;
    text-transform: uppercase;
    line-height: 1.05;
  }
  .brand-mark .square { width: 14px; height: 14px; background: var(--ink); flex: none; }
  .person { position: absolute; left: 150px; top: 128px; text-align: center; width: 230px; }
  .person-name { font-weight: 700; font-size: 22px; letter-spacing: 0.5px; text-transform: uppercase; }
  .person-role { font-size: 15px; margin-top: 3px; }
  .address {
    position: absolute; right: 34px; top: 160px;
    font-size: 14px; line-height: 1.45; text-align: right;
  }
  .divider {
    position: absolute; left: 28px; right: 28px; top: 212px;
    height: 1px; background: var(--rule);
  }
  .contacts {
    position: absolute; left: 34px; top: 226px;
    list-style: none; font-size: 14px; line-height: 1.7;
  }
  .contacts li { display: flex; align-items: center; gap: 8px; }
  .contacts svg { width: 11px; height: 11px; flex: none; }

  /* Back: brand side */
  .brand-back {
    position: absolute; inset: 0;
    display: flex; align-items: center; justify-content: center; gap: 14px;
    font-weight: 700; font-size: 38px; letter-spacing: 1px;
    text-transform: uppercase; text-align: left; line-height: 1.05;
  }
  .brand-back .square { width: 26px; height: 26px; background: var(--ink); flex: none; }
</style>
</head>
<body>
  <section class="card card-front">
    <div class="brand-mark"><span class="square"></span><span>Harwell<br>Building Group</span></div>
    <div class="person">
      <p class="person-name">Daniel Oakes</p>
      <p class="person-role">CEO/Founder</p>
    </div>
    <p class="address">28 Fernleigh St<br>Dandenong, VIC 3175</p>
    <div class="divider"></div>
    <ul class="contacts">
      <li><svg viewBox="0 0 12 12"><path fill="#fff" d="M2.5 1l2 2.2-1 1.3c.8 1.6 1.9 2.7 3.5 3.5l1.3-1 2.2 2-1.2 1.8C5 10.4 1.6 7 1 2.2z"/></svg>0400 555 018</li>
      <li><svg viewBox="0 0 12 12"><rect x="1" y="2.5" width="10" height="7" fill="none" stroke="#fff" stroke-width="1.2"/><path d="M1 2.5l5 4 5-4" fill="none" stroke="#fff" stroke-width="1.2"/></svg>info@harwellbuilding.com.au</li>
      <li><svg viewBox="0 0 12 12"><circle cx="6" cy="6" r="5" fill="none" stroke="#fff" stroke-width="1.2"/><path d="M1 6h10M6 1c-2.5 3-2.5 7 0 10M6 1c2.5 3 2.5 7 0 10" fill="none" stroke="#fff" stroke-width="1"/></svg>harwellbuilding.com.au</li>
    </ul>
  </section>

  <section class="card card-back">
    <div class="brand-back"><span class="square"></span><span>Harwell<br>Building Group</span></div>
  </section>
</body>
</html>
```